Vantoq Business Card Project showing the logo and a marbo image on the rear

Design a whacky but professional business card, the logo is for the front and the Marbo image is for the rear. Happy to consider other open source Marbo Images if the designer wants to select one from the web. Vantoq is a competitor to OMB.com.au and Pellory.com.au and is based around every property in Australia

Target Market(s)

Business

Contact Information for Business Card

Name, Title, Email, Web, Phone Number

Font styles to use
Other font styles liked:
• avenir

Requirements
Must have
• Image on Back logo on front
Nice to have
• Happy to consider other images on rear, preftably Colin Marbo. Image supplied I own, we can use open source other Marbo Images

```html
<!DOCTYPE html>
<html lang="en">
<head>
<meta charset="utf-8">
<title>Vantoq Business Card</title>
<link rel="stylesheet" href="https://fonts.googleapis.com/css2?family=Nunito+Sans:wght@400;700;800&display=swap">
<style>
  :root {
    --page-bg: #2b2b2d;
    --card-dark: #232323;
    --brand-orange: #f39324;
    --text-light: #f4f4f4;
    --sky-blue: #3d9be0;
    --night-blue: #2a5db8;
    --city-red: #e0453b;
    --city-yellow: #f3c523;
    --city-green: #2f8a3a;
    --city-teal: #27a7c6;
  }
  * { margin: 0; padding: 0; box-sizing: border-box; }
  html, body {
    width: 1200px; height: 900px; overflow: hidden;
    background: var(--page-bg);
    font-family: "Nunito Sans", sans-serif;
  }
  .card {
    position: absolute;
    width: 640px; height: 370px;
    border-radius: 22px;
    overflow: hidden;
  }
  .card--artwork { left: 420px; top: 50px; }
  .card--contact { left: 140px; top: 470px; background: var(--card-dark); }

  .artwork-fill {
    position: absolute; inset: 0;
    background:
      linear-gradient(180deg, rgba(0,0,0,0) 40%, rgba(0,0,0,0.15) 100%),
      linear-gradient(90deg, var(--sky-blue) 0%, var(--night-blue) 100%);
  }
  .artwork-fill::after {
    content: ""; position: absolute; left: 0; right: 0; bottom: 0; height: 62%;
    background: linear-gradient(90deg,
      var(--city-red) 0%, var(--city-yellow) 22%, var(--city-green) 42%,
      var(--brand-orange) 62%, var(--city-red) 80%, var(--city-teal) 100%);
  }
  .artwork-brand {
    position: absolute; left: 200px; top: 130px;
    display: flex; align-items: center; gap: 18px;
  }
  .brand-square {
    width: 58px; height: 58px; background: var(--brand-orange);
  }
  .brand-name {
    font-weight: 800; font-size: 64px; color: #ffffff; letter-spacing: 1px; line-height: 1;
  }

  .contact-block {
    position: absolute; left: 50px; top: 46px; width: 260px;
    color: var(--text-light);
  }
  .person-name {
    font-weight: 800; font-size: 25px; color: var(--brand-orange);
    letter-spacing: 1px; text-transform: uppercase; line-height: 1.1;
  }
  .person-title { font-size: 17px; margin-top: 2px; }
  .rule { height: 1.5px; background: var(--brand-orange); margin: 14px 0; }
  .address { font-size: 18px; line-height: 1.35; }
  .contact-line {
    display: flex; align-items: center; gap: 10px;
    font-size: 18px; line-height: 1.45;
  }
  .contact-line svg { width: 14px; height: 14px; flex: none; fill: var(--brand-orange); }
  .web-accent { color: var(--brand-orange); }

  .contact-brand {
    position: absolute; right: 56px; bottom: 80px;
    display: flex; align-items: center; gap: 18px;
  }
  .contact-brand .brand-square { width: 54px; height: 54px; }
  .contact-brand .brand-name { font-size: 58px; }
</style>
</head>
<body>

  <section class="card card--artwork">
    <div class="artwork-fill" role="img" aria-label="Colourful Colin Marbo style cityscape artwork of playful buildings under a sunny day and starry night sky"></div>
    <div class="artwork-brand">
      <span class="brand-square"></span>
      <span class="brand-name">Vantoq</span>
    </div>
  </section>

  <section class="card card--contact">
    <div class="contact-block">
      <h1 class="person-name">Owen Carrick</h1>
      <p class="person-title">Executive Producer</p>
      <div class="rule"></div>
      <p class="address">418 W Harlow Street<br>Brennock County name 4172</p>
      <div class="rule"></div>
      <p class="contact-line">
        <svg viewBox="0 0 24 24"><path d="M6.6 10.8a15.1 15.1 0 0 0 6.6 6.6l2.2-2.2c.3-.3.7-.4 1-.2 1.1.4 2.3.6 3.6.6.6 0 1 .4 1 1V20c0 .6-.4 1-1 1A17 17 0 0 1 3 4c0-.6.4-1 1-1h3.5c.6 0 1 .4 1 1 0 1.3.2 2.5.6 3.6.1.3 0 .7-.2 1z"/></svg>
        415-287-6094
      </p>
      <p class="contact-line">
        <svg viewBox="0 0 24 24"><path d="M2 5h20v14H2z M2 5l10 8 10-8" fill="var(--brand-orange)" stroke="var(--card-dark)" stroke-width="1.5"/></svg>
        Owen@vantoq.com.au
      </p>
      <p class="contact-line">
        <svg viewBox="0 0 24 24"><circle cx="12" cy="12" r="10"/><path d="M2 12h20M12 2c3 3 3 17 0 20M12 2c-3 3-3 17 0 20" fill="none" stroke="var(--card-dark)" stroke-width="1.5"/></svg>
        <span>www.<span class="web-accent">vantoq</span>.com.au</span>
      </p>
    </div>

    <div class="contact-brand">
      <span class="brand-square"></span>
      <span class="brand-name">Vantoq</span>
    </div>
  </section>

</body>
</html>
```